Veltrane Group Business Card Design

The CEO is looking for a new trendy look for his business card.
You can stay with current branding or come up with something new/creative. It can be 3D, including Medical Office buildings. You can use our logo in a variety of colors. Please include name, title, company name, company website, email address, cell number

Target Market(s)

Real Estate Development and Construction

Industry/Entity Type

Health care real estate

Contact Information for Business Card

Rohesh Kamdar, CEO M-604.781.2249 E-roheshkamdar@veltrane.com Address:4180 Lindqvist Ave, Tampa, FL 33482 www.veltrane.com

Font styles to use
Other font styles liked:
• Be creative

Requirements
Must have
• Creative, trendy look
Nice to have
• Please go to our website to get a feel- www. veltrane.com
Should not have
• small fonts

```html
<!DOCTYPE html>
<html lang="en">
<head>
<meta charset="utf-8">
<title>Veltrane Group — Business Card</title>
<link rel="stylesheet" href="https://fonts.googleapis.com/css2?family=Poppins:wght@400;600;700;800&display=swap">
<style>
  :root {
    --navy: #1d3052;
    --red: #b5202b;
    --white: #ffffff;
    --backdrop: #e7e5e2;
  }
  * { margin: 0; padding: 0; box-sizing: border-box; }
  html, body {
    width: 1200px;
    height: 842px;
    overflow: hidden;
    background: var(--backdrop);
    font-family: "Poppins", sans-serif;
  }
  .canvas {
    position: relative;
    width: 1200px;
    height: 842px;
  }
  .card {
    position: absolute;
    top: 272px;
    width: 520px;
    height: 297px;
    overflow: hidden;
    box-shadow: 0 10px 28px rgba(0,0,0,0.18);
  }

  /* Contact side */
  .card-contact {
    left: 60px;
    background: var(--red);
    border-top: 18px solid var(--navy);
    border-bottom: 18px solid var(--navy);
    color: var(--white);
    display: flex;
    flex-direction: column;
    align-items: center;
    justify-content: center;
    text-align: center;
  }
  .person-name {
    font-weight: 700;
    font-size: 22px;
    letter-spacing: 1.5px;
    text-transform: uppercase;
    line-height: 1.1;
  }
  .person-title {
    font-size: 14px;
    line-height: 1.2;
    margin-top: 2px;
  }
  .rule {
    width: 62px;
    height: 2px;
    background: var(--navy);
    margin: 8px 0 9px;
  }
  .address, .contact-lines {
    font-size: 14.5px;
    line-height: 1.3;
  }

  /* Brand side */
  .card-brand {
    left: 620px;
    background: var(--navy);
  }
  .edge-block {
    position: absolute;
    background: var(--red);
    width: 30px;
    height: 72px;
  }
  .edge-line {
    position: absolute;
    background: var(--white);
    width: 5px;
    height: 72px;
  }
  .edge-left .edge-block { left: 0; top: 150px; }
  .edge-left .edge-line { left: 40px; top: 150px; }
  .edge-right .edge-block { right: 0; top: 50px; }
  .edge-right .edge-line { right: 40px; top: 50px; }
  .brand-name {
    position: absolute;
    left: 0;
    right: 0;
    top: 112px;
    text-align: center;
    font-weight: 800;
    font-size: 44px;
    letter-spacing: -1px;
    color: var(--red);
    line-height: 1;
  }
</style>
</head>
<body>
  <main class="canvas">
    <section class="card card-contact" aria-label="Business card, contact side">
      <h1 class="person-name">Rohesh Kamdar</h1>
      <p class="person-title">CEO</p>
      <div class="rule"></div>
      <p class="address">4180 Lindqvist Ave<br>Tampa, FL 33482</p>
      <div class="rule"></div>
      <p class="contact-lines">604.781.2249<br>roheshkamdar@veltrane.com<br>www.veltrane.com</p>
    </section>

    <section class="card card-brand" aria-label="Business card, brand side">
      <div class="edge-left">
        <span class="edge-block"></span>
        <span class="edge-line"></span>
      </div>
      <div class="edge-right">
        <span class="edge-block"></span>
        <span class="edge-line"></span>
      </div>
      <p class="brand-name">Veltrane Group</p>
    </section>
  </main>
</body>
</html>
```